4th Generation Family Business Needs a New Card Design!

We are a family owned 4th Generation company. We are based in the Sydney, Australia area and we are desperately in need of a more modern and classy card. We are monumental masons who design, supply & erect lasting memorials throughout cemeteries in Sydney. Our customers are normally in a period of grieving. I have attached logo files that will need to be implemented on the card. Company was established 1935. Australian Owned and Operated. Card needs to be designed to PIXO.com specification.

Target Market(s)

Our target market is based upon people that a grieving for family members that have passed away. We also deal with alot of companies that own and operate cemeteries.

Industry/Entity Type

Business

Contact Information for Business Card

Simon Harcourt, Operations Manager, 0417293086, simon@harcourtmemorials.com.au
Lewis Harcourt, Director, 0491630572, lewis@harcourtmemorials.com.au
Phone # 02 9561 3048
Website: www.harcourtmemorials.com.au
Address: Suite 17, 8 Palfrey Lane, West Carlow, Sydney NSW 2156

Font styles to use
Serif
Decorative
Script

Requirements
Must have
• Would like to see the logo nicely implemented with a modern design. Embossed lettering would be a nice additive.

```html
<!DOCTYPE html>
<html lang="en">
<head>
<meta charset="utf-8">
<title>Harcourt Memorials – Business Card</title>
<link href="https://fonts.googleapis.com/css2?family=Cinzel:wght@400;600&family=Libre+Baskerville&display=swap" rel="stylesheet">
<style>
  :root {
    --backdrop: #d9d9d9;
    --card: #fbfbfb;
    --ink: #1c1c1c;
    --gold: #d8ac1c;
    --gold-dark: #c39a12;
    --faint: #ececec;
  }
  * { box-sizing: border-box; margin: 0; padding: 0; }
  html, body { width: 1200px; height: 576px; overflow: hidden; }
  body { background: var(--backdrop); position: relative; }

  .card {
    position: absolute;
    top: 138px;
    height: 292px;
    background: var(--card);
    overflow: hidden;
  }
  .card::after {
    content: "";
    position: absolute;
    left: 0; right: 0; bottom: 0;
    height: 11px;
    background: linear-gradient(to bottom, var(--gold), var(--gold-dark));
  }
  .card--front { left: 80px; width: 486px; }
  .card--back  { left: 602px; width: 482px; }

  .brand {
    position: absolute;
    font-family: "Cinzel", serif;
    font-weight: 400;
    color: var(--ink);
    text-align: center;
    line-height: 1;
  }
  .brand__name { display: block; letter-spacing: 1px; }
  .brand__sub { display: block; letter-spacing: 3px; }

  .card--front .brand { left: 0; right: 0; top: 108px; }
  .card--front .brand__name { font-size: 38px; }
  .card--front .brand__sub { font-size: 14px; margin-top: 10px; }

  .card--back .brand { left: 18px; width: 180px; top: 70px; }
  .card--back .brand__name { font-size: 27px; }
  .card--back .brand__sub { font-size: 10px; margin-top: 8px; }

  .backdrop-mark {
    position: absolute;
    right: -20px; top: 30px;
    width: 200px; height: 200px;
    background: var(--faint);
  }

  .person {
    position: absolute;
    right: 28px; top: 36px;
    text-align: right;
  }
  .person__name {
    font-family: "Cinzel", serif;
    font-weight: 600;
    font-size: 18px;
    color: var(--ink);
    letter-spacing: 0.5px;
  }
  .person__role {
    font-family: "Libre Baskerville", serif;
    font-size: 10px;
    color: var(--ink);
    margin-top: 4px;
  }

  .contacts {
    position: absolute;
    left: 26px; top: 175px;
    list-style: none;
    font-family: "Libre Baskerville", serif;
    font-size: 11.5px;
    color: var(--ink);
  }
  .contacts li {
    display: flex; align-items: center;
    height: 17.5px;
  }
  .contacts svg { width: 10px; height: 10px; margin-right: 12px; fill: var(--gold); }
  .address {
    position: absolute;
    left: 26px; top: 247px;
    font-family: "Libre Baskerville", serif;
    font-size: 11.5px;
    color: var(--ink);
  }
</style>
</head>
<body>

<section class="card card--front">
  <div class="brand">
    <span class="brand__name">HARCOURT</span>
    <span class="brand__sub">MEMORIALS</span>
  </div>
</section>

<section class="card card--back">
  <div class="backdrop-mark"></div>

  <div class="brand">
    <span class="brand__name">HARCOURT</span>
    <span class="brand__sub">MEMORIALS</span>
  </div>

  <div class="person">
    <div class="person__name">SIMON HARCOURT</div>
    <div class="person__role">Operations Manager</div>
  </div>

  <ul class="contacts">
    <li>
      <svg viewBox="0 0 10 10"><path d="M2 0.5l2 2-1 1.2c.6 1.3 1.6 2.3 2.9 2.9l1.2-1 2 2-1.3 1.8C4 9.2 0.8 6 .2 1.8z"/></svg>
      0491630572
    </li>
    <li>
      <svg viewBox="0 0 10 10"><path d="M0 3c0-1.5 10-1.5 10 0v1.3H7.5V3h-5v1.3H0zM2 5h6l1.5 4h-9z"/></svg>
      02 9561 3048
    </li>
    <li>
      <svg viewBox="0 0 10 10"><path d="M0 1.5h10v7H0zM.6 2l4.4 3.4L9.4 2"/><path d="M.6 2l4.4 3.4L9.4 2" fill="none" stroke="#fbfbfb" stroke-width=".8"/></svg>
      lewis@harcourtmemorials.com.au
    </li>
    <li>
      <svg viewBox="0 0 10 10"><circle cx="5" cy="5" r="4.6"/><path d="M.5 5h9M5 .5v9M2 2.4c2 1 4 1 6 0M2 7.6c2-1 4-1 6 0" fill="none" stroke="#fbfbfb" stroke-width=".6"/></svg>
      www.harcourtmemorials.com.au
    </li>
  </ul>

  <p class="address">Suite 17, 8 Palfrey Lane, West Carlow, Sydney NSW 2156</p>
</section>

</body>
</html>
```